Website for IT technology distribution company

Small business distributor of remote IT/Telecoms technology services in Canada

Looking for a bold, clean and professional design for WordPress. We would like a web site design from a designer who may be able to help us upload the site to WordPress (Ideally CSS files).
The website will have the following pages:
1) Home
2) Register
3) Packages
4) Contact

I am also attaching the company logo (with sourcefile, images for page 1 and details on wording/content for website)

Design must use colors that compliment the logo

Must Have:
- Must contain the logo in the header

Should Not Have:
- must not be blog or magazine style layout or look and feel

Industry/Entity Type

Business

```html
<!DOCTYPE html>
<html lang="en">
<head>
<meta charset="utf-8">
<title>Tarvelco Solutions Ltd — Home</title>
<link href="https://fonts.googleapis.com/css2?family=Open+Sans:wght@400;600;700&family=Oxygen:wght@400;700&display=swap" rel="stylesheet">
<style>
  :root {
    --brand-red: #e3242b;
    --slate: #5b6679;
    --slate-dark: #3f4d63;
    --link-blue: #3c5677;
    --text-grey: #5c5f66;
    --muted-grey: #8a8f98;
    --card-border: #dfe1e4;
    --footer-bg: #5b6a80;
    --footer-text: #e8ecf2;
    --footer-muted: #b9c2cf;
    --white: #ffffff;
  }
  * { box-sizing: border-box; margin: 0; padding: 0; }
  html, body { width: 1170px; height: 1200px; overflow: hidden; }
  body {
    position: relative;
    background: var(--white);
    font-family: "Open Sans", Arial, sans-serif;
    color: var(--text-grey);
  }
  .top-rule { position: absolute; left: 0; top: 0; width: 100%; height: 4px; background: #d9dcdf; }
  .stage-band {
    position: absolute; left: 0; top: 114px; width: 100%; height: 222px;
    background: linear-gradient(to bottom, #ffffff 0%, #e6e8eb 100%);
  }
  .brand {
    position: absolute; left: 138px; top: 40px;
    display: flex; align-items: center; gap: 8px;
    font-weight: 700; color: var(--slate); text-decoration: none;
  }
  .brand-mark { width: 14px; height: 14px; background: var(--brand-red); }
  .brand-name { font-size: 29px; letter-spacing: 1px; line-height: 1; }
  .brand-sub { position: absolute; left: 160px; top: 84px; font-size: 10px; font-weight: 700; color: var(--brand-red); letter-spacing: .5px; }
  .main-nav { position: absolute; top: 61px; left: 627px; display: flex; }
  .main-nav a {
    display: block; height: 38px; line-height: 38px; padding: 0 20px;
    font-size: 15px; text-transform: uppercase; color: var(--slate); text-decoration: none;
    margin-right: 4px;
  }
  .main-nav a.is-active { background: var(--brand-red); color: var(--white); border-radius: 19px; }
  .hero {
    position: absolute; left: 135px; top: 120px; width: 901px; height: 378px;
    border-radius: 4px; overflow: hidden;
  }
  .hero-art {
    position: absolute; inset: 0;
    background:
      radial-gradient(circle at 50% 42%, #d9232a 0, #c9262d 17%, rgba(230,120,130,.6) 30%, rgba(240,190,195,.4) 60%, rgba(245,220,222,.3) 100%),
      linear-gradient(135deg, #e07a82 0%, #f3d3d6 45%, #e9a0a6 100%);
  }
  .hero-title {
    position: absolute; left: 0; right: 0; top: 150px; text-align: center;
    font-size: 33px; font-weight: 700; color: var(--white); text-transform: uppercase;
    text-shadow: 0 2px 4px rgba(0,0,0,.35); letter-spacing: .3px; line-height: 42px;
  }
  .hero-sub {
    position: absolute; left: 0; right: 0; top: 193px; text-align: center;
    font-size: 22px; color: var(--white); text-transform: uppercase; line-height: 30px;
    text-shadow: 0 2px 4px rgba(0,0,0,.35);
  }
  .hero-dots { position: absolute; left: 425px; top: 355px; display: flex; gap: 5px; }
  .hero-dots span { width: 11px; height: 11px; border-radius: 50%; background: var(--white); opacity: .92; }
  .features { position: absolute; left: 138px; top: 516px; display: flex; gap: 12px; }
  .feature-card {
    width: 216px; height: 181px; border: 1px solid var(--card-border); background: var(--white);
    box-shadow: 0 1px 2px rgba(0,0,0,.04); padding: 8px 9px 0;
  }
  .feature-photo { width: 197px; height: 100px; border: 1px solid #cfd3d8; }
  .feature-photo.is-tech { background: linear-gradient(135deg, #2f3d55, #6a88a8 55%, #e6e6e6); }
  .feature-photo.is-support { background: linear-gradient(135deg, #f4f4f4, #d9c6bb 45%, #f8f8f8); }
  .feature-photo.is-telecom { background: linear-gradient(135deg, #34476a, #8fa0ae 55%, #d8d2c6); }
  .feature-photo.is-office { background: linear-gradient(135deg, #cfd8e2, #f3f5f7 50%, #c8cfd6); }
  .feature-title { margin-top: 8px; font-size: 16px; font-weight: 400; color: var(--brand-red); padding-left: 3px; line-height: 22px; }
  .feature-text { margin-top: 0; font-size: 10.5px; line-height: 14px; color: var(--muted-grey); padding-left: 3px; white-space: nowrap; }
  .divider {
    position: absolute; left: 135px; top: 728px; width: 901px; height: 20px;
    border-top: 1px solid #eceef0;
    background: radial-gradient(ellipse at 50% 0, rgba(0,0,0,.05), rgba(0,0,0,0) 70%);
  }
  .welcome { position: absolute; left: 136px; top: 768px; width: 620px; }
  .section-title { font-family: "Oxygen", "Open Sans", sans-serif; font-weight: 400; font-size: 28px; color: var(--slate-dark); line-height: 36px; }
  .welcome p { font-size: 11.5px; line-height: 22px; color: var(--text-grey); padding-left: 2px; white-space: nowrap; }
  .welcome .lead { margin-top: 5px; }
  .welcome .gap { margin-top: 9px; }
  .blog { position: absolute; left: 784px; top: 768px; width: 250px; }
  .blog .section-title { font-size: 24px; }
  .post { margin-top: 15px; padding-left: 2px; }
  .blog .post:first-of-type { margin-top: 7px; }
  .post-title { font-size: 13px; font-weight: 400; color: var(--link-blue); line-height: 18px; }
  .post-excerpt { margin-top: 3px; font-size: 11px; line-height: 17.5px; color: var(--muted-grey); }
  .site-footer { position: absolute; left: 0; top: 1096px; width: 100%; height: 104px; background: var(--footer-bg); }
  .footer-nav { position: absolute; left: 134px; top: 28px; display: flex; align-items: center; font-size: 12.5px; font-weight: 600; }
  .footer-nav a { color: var(--footer-text); text-decoration: none; text-transform: uppercase; }
  .footer-nav .sep { color: var(--footer-text); margin: 0 14px; }
  .copyright { position: absolute; left: 135px; top: 52px; font-size: 10.5px; color: var(--footer-muted); }
  .social { position: absolute; left: 956px; top: 29px; display: flex; gap: 8px; }
  .social span { width: 22px; height: 22px; border-radius: 50%; background: var(--white); }
</style>
</head>
<body>
  <div class="top-rule"></div>
  <div class="stage-band"></div>

  <header class="site-header">
    <a class="brand" href="#"><span class="brand-mark"></span><span class="brand-name">TARVELCO</span></a>
    <span class="brand-sub">Solutions Ltd</span>
    <nav class="main-nav">
      <a class="is-active" href="#">Home</a>
      <a href="#">Register</a>
      <a href="#">Packages</a>
      <a href="#">Contact</a>
    </nav>
  </header>

  <section class="hero">
    <div class="hero-art" role="img" aria-label="Red globe connected by cables to laptops and monitors over a binary code background"></div>
    <h1 class="hero-title">Aliquam nec erat purus cursus inter</h1>
    <p class="hero-sub">Vestibulum ligula augue bibendum</p>
    <div class="hero-dots"><span></span><span></span><span></span><span></span></div>
  </section>

  <section class="features">
    <article class="feature-card">
      <div class="feature-photo is-tech" role="img" aria-label="Engineer with a tablet in a server room"></div>
      <h3 class="feature-title">What We Do</h3>
      <p class="feature-text">Aliquam nec erat at purus cursus inter-<br>dum Vestibulum ligula augue bi</p>
    </article>
    <article class="feature-card">
      <div class="feature-photo is-support" role="img" aria-label="Support agent wearing a headset"></div>
      <h3 class="feature-title">Services Provide</h3>
      <p class="feature-text">Aliquam nec erat at purus cursus inter-<br>dum Vestibulum ligula augue bi</p>
    </article>
    <article class="feature-card">
      <div class="feature-photo is-telecom" role="img" aria-label="Technician working at a network cabinet"></div>
      <h3 class="feature-title">IT Telecom</h3>
      <p class="feature-text">Aliquam nec erat at purus cursus inter-<br>dum Vestibulum ligula augue bi</p>
    </article>
    <article class="feature-card">
      <div class="feature-photo is-office" role="img" aria-label="Call centre staff at computer desks"></div>
      <h3 class="feature-title">Our Packages</h3>
      <p class="feature-text">Aliquam nec erat at purus cursus inter-<br>dum Vestibulum ligula augue bi</p>
    </article>
  </section>

  <div class="divider"></div>

  <main class="welcome">
    <h2 class="section-title">Welcome to Our Website Mainpage</h2>
    <p class="lead">Imagine immediate access to highly trained Quindrel engineers, without the cost and expense of paying them for a<br>site visit. TARVELCO is a Canadian based consulting and distributor of Remote Quindrel technical services.<br>Are you or your customer’s network running slow; is there a switch or WLAN issue that needs looking at? Need to<br>deploy a PBX with tight deadlines or when your resource scheduling doesn’t allow? A remote Quindrel expertise is the<br>answer! Cost efficient, fast and you won’t be paying for travel times and lunch breaks.</p>
    <p class="gap">TARVELCO is the sole distributor of Velmoryx remote services in Canada. Velmoryx is a UK based leader in providing<br>remote technical services. A remote Quindrel engineer is better for your budget and ICT infrastructure. Efficient net-<br>work optimization ensures you are getting the most out of your Quindrel network technology, ensuring your commu-<br>nications are always up to date, and up to speed.<br>We guarantee immediate, efficient service, anywhere in the world</p>
  </main>

  <aside class="blog">
    <h2 class="section-title">Latest Blog Post</h2>
    <div class="post">
      <h4 class="post-title">Donec convallis pede venenatis</h4>
      <p class="post-excerpt">Phasellus felis dolor scelerisque a tempus eget lobortis id libero Donec</p>
    </div>
    <div class="post">
      <h4 class="post-title">Pellentesque faucibus</h4>
      <p class="post-excerpt">Phasellus felis dolor scelerisque a tempus eget lobortis id libero Donec</p>
    </div>
    <div class="post">
      <h4 class="post-title">Etiam eu urna Sed</h4>
      <p class="post-excerpt">Scelerisque a tempus eget lobortis id libero</p>
    </div>
  </aside>

  <footer class="site-footer">
    <nav class="footer-nav">
      <a href="#">Home</a><span class="sep">|</span>
      <a href="#">Register</a><span class="sep">|</span>
      <a href="#">Packages</a><span class="sep">|</span>
      <a href="#">Contact</a>
    </nav>
    <p class="copyright">© 2014 Company Name.&nbsp; All right reserved.&nbsp; Term of Use</p>
    <div class="social" aria-label="Social links"><span></span><span></span><span></span></div>
  </footer>
</body>
</html>
```